Create a memorable Stationary for Security Software Company

Velbrantix is the worldwide leader in securing the Internet. Making Internet communications and critical data secure, reliable and available everywhere has been and continues to be our ongoing vision. We are committed to staying focused on real customer needs and to developing new and innovative security solutions that redefine the security landscape.

Industry/Entity Type

Internet

Font styles to use
Serif
Sans Serif
Script

Colors
0792cd
33a6d7
85cae6

```html
<!DOCTYPE html>
<html lang="en">
<head>
<meta charset="utf-8">
<title>Velbrantix Business Card</title>
<link href="https://fonts.googleapis.com/css2?family=Open+Sans:wght@400;600;700&display=swap" rel="stylesheet">
<style>
  :root {
    --brand-deep: #0792cd;
    --brand-mid: #33a6d7;
    --brand-light: #85cae6;
    --sky-pale: #b9e2f3;
    --ink: #4a4a4a;
    --paper: #ffffff;
    --stage: #e9eef1;
  }
  html, body {
    margin: 0; padding: 0; width: 1200px; height: 843px; overflow: hidden;
    background: var(--stage);
    font-family: "Open Sans", sans-serif;
  }
  .stage {
    position: relative; width: 1200px; height: 843px;
    display: flex; flex-direction: column; align-items: center; justify-content: center; gap: 56px;
  }
  .card {
    position: relative; width: 630px; height: 360px; border-radius: 22px; overflow: hidden;
    box-shadow: 0 10px 28px rgba(0,0,0,0.18);
  }
  .card-front { background: var(--paper); }
  .cloud-panel { position: absolute; inset: 0; }
  .contact-block { position: absolute; left: 48px; top: 46px; color: var(--ink); }
  .person-name { margin: 0; font-size: 27px; font-weight: 700; color: var(--brand-mid); letter-spacing: 0.2px; }
  .person-role { margin: 2px 0 0; font-size: 16px; color: #6a6a6a; }
  .address { margin: 34px 0 6px; font-size: 16px; line-height: 1.35; }
  .contact-list { list-style: none; margin: 0; padding: 0; font-size: 16px; line-height: 1.55; }
  .contact-list li { display: flex; align-items: center; gap: 10px; }
  .contact-list svg { width: 15px; height: 15px; flex: none; }
  .brand-mark {
    position: absolute; display: flex; align-items: center; gap: 10px;
    font-weight: 700; color: var(--paper);
  }
  .brand-dot { border-radius: 50%; background: var(--brand-deep); }
  .card-front .brand-mark { right: 44px; top: 196px; font-size: 25px; }
  .card-front .brand-dot { width: 26px; height: 26px; }
  .card-back { background: linear-gradient(160deg, var(--sky-pale) 0%, var(--brand-light) 50%, var(--brand-mid) 100%); }
  .card-back .brand-mark { left: 50%; top: 50%; transform: translate(-50%, -60%); font-size: 38px; }
  .card-back .brand-dot { width: 36px; height: 36px; }
  .back-web {
    position: absolute; left: 0; right: 0; bottom: 40px; text-align: center;
    font-size: 15px; letter-spacing: 6px; color: var(--brand-deep); opacity: 0.55;
  }
</style>
</head>
<body>
<main class="stage">
  <section class="card card-front">
    <svg class="cloud-panel" viewBox="0 0 630 360" aria-hidden="true">
      <defs>
        <linearGradient id="cloudFill" x1="0" y1="0" x2="0.4" y2="1">
          <stop offset="0" stop-color="#a9dcf1"/>
          <stop offset="1" stop-color="#5fb7df"/>
        </linearGradient>
      </defs>
      <path d="M450 360 C405 345 385 312 400 285 C352 270 350 218 388 202 C356 176 372 122 420 128 C414 86 458 60 494 82 C510 38 574 40 592 72 C606 58 620 56 630 60 L630 360 Z"
            fill="url(#cloudFill)" stroke="#33a6d7" stroke-width="2.5"/>
    </svg>
    <div class="contact-block">
      <h1 class="person-name">Mara Kellworth</h1>
      <p class="person-role">CEO/Founder</p>
      <p class="address">4120 Larchmont Way<br>Fairbrook, Oregon 97311</p>
      <ul class="contact-list">
        <li><svg viewBox="0 0 16 16"><path fill="#0792cd" d="M4 1l2.5 3-1.5 2c1 2 2.5 3.5 4.5 4.5l2-1.5 3 2.5-1.5 2.5C8 15 1 8 1.5 2.5z"/></svg>503 218 6647</li>
        <li><svg viewBox="0 0 16 16"><rect x="4" y="1" width="8" height="5" fill="#0792cd"/><rect x="1" y="6" width="14" height="7" rx="1" fill="#0792cd"/><rect x="4" y="10" width="8" height="5" fill="#fff" stroke="#0792cd"/></svg>503 218 6650</li>
        <li><svg viewBox="0 0 16 16"><rect x="1" y="3" width="14" height="10" rx="1" fill="#0792cd"/><path d="M1.5 4l6.5 5 6.5-5" fill="none" stroke="#fff" stroke-width="1.3"/></svg>mara@velbrantix.com</li>
        <li><svg viewBox="0 0 16 16"><circle cx="8" cy="8" r="7" fill="#0792cd"/><path d="M1 8h14M8 1c-3 3-3 11 0 14M8 1c3 3 3 11 0 14" fill="none" stroke="#fff" stroke-width="1"/></svg>www.velbrantix.com</li>
      </ul>
    </div>
    <div class="brand-mark"><span class="brand-dot"></span>Velbrantix</div>
  </section>

  <section class="card card-back">
    <div class="brand-mark"><span class="brand-dot"></span>Velbrantix</div>
    <p class="back-web">www.velbrantix.com</p>
  </section>
</main>
</body>
</html>
```